Business Card Design Project

i need a bussines car design
Velora Clinical Hypnotherapy

Daniel Wexford
Psychotherapy & Hypnosis

84261937 /0427591628

back of the card appoinment space.

file was provided on a PDF, LOgo , use the blu colorsa as well , elegant, clear,

Target Market(s)

young professional, caucasian , young mothers.

Industry/Entity Type

Business

```html
<!DOCTYPE html>
<html lang="en">
<head>
<meta charset="utf-8">
<title>Velora Clinical Hypnotherapy – Business Card</title>
<link rel="stylesheet" href="https://fonts.googleapis.com/css2?family=Source+Sans+3:wght@400;600;700&display=swap">
<style>
  :root {
    --backdrop: #e9e9ea;
    --card: #ffffff;
    --brand-blue: #0a72bb;
    --brand-blue-soft: #1f9ad0;
    --teal: #1ba0c9;
    --swoosh-grey: #8e8f91;
    --text-grey: #7b7c7e;
    --text-dark: #55575a;
    --photo-top: #d9d4cd;
    --photo-bottom: #efe3d3;
  }
  * { box-sizing: border-box; margin: 0; padding: 0; }
  html, body {
    width: 1200px; height: 789px; overflow: hidden;
    background: var(--backdrop);
    font-family: "Source Sans 3", "Myriad Pro", Arial, sans-serif;
  }
  .card {
    position: absolute;
    width: 368px; height: 651px;
    background: var(--card);
    border-radius: 20px;
    overflow: hidden;
    box-shadow: 0 2px 10px rgba(0,0,0,0.15);
  }
  .card--front { left: 225px; top: 76px; }
  .card--back  { left: 625px; top: 74px; }
  .abs { position: absolute; left: 0; width: 100%; text-align: center; }

  /* front */
  .brand-mark {
    position: absolute; left: 154px; top: 40px;
    width: 60px; height: 60px; border-radius: 50%;
    background: var(--brand-blue);
  }
  .brand-name { top: 116px; font-size: 27px; font-weight: 400; color: var(--brand-blue); letter-spacing: 0.3px; }
  .brand-rule { position: absolute; left: 64px; top: 152px; width: 240px; height: 1px; background: var(--text-grey); }
  .brand-url { top: 154px; font-size: 11px; color: var(--text-dark); letter-spacing: 0.6px; }
  .person-name { top: 197px; font-size: 17px; color: var(--teal); }
  .person-role { top: 220px; font-size: 15px; color: var(--text-grey); }
  .portrait {
    position: absolute; left: 66px; top: 262px; width: 236px; height: 312px;
    background: linear-gradient(180deg, var(--photo-top), var(--photo-bottom));
    border-radius: 40px 40px 0 0;
  }
  .wave { position: absolute; left: 0; bottom: 0; width: 368px; height: 110px; }
  .front-phones { top: 600px; font-size: 15px; color: #fff; }
  .front-url { top: 620px; font-size: 17px; color: #fff; }

  /* back */
  .practice-name { top: 24px; font-size: 18px; font-weight: 700; color: var(--brand-blue); }
  .practice-line { font-size: 16px; color: var(--text-grey); }
  .practice-line--phone { top: 46px; }
  .practice-line--address { top: 68px; }
  .practice-email { top: 91px; font-size: 12px; font-weight: 700; color: var(--text-dark); }
  .appointments-title { top: 153px; font-size: 17px; font-weight: 700; color: var(--brand-blue); }
  .appointment-list { position: absolute; left: 34px; top: 194px; list-style: none; }
  .appointment-list li { height: 42px; font-size: 16px; color: var(--text-grey); white-space: nowrap; }
  .reschedule { top: 467px; font-size: 15px; line-height: 20px; color: var(--brand-blue); }
  .registration { top: 614px; font-size: 17px; color: #fff; }
</style>
</head>
<body>

<section class="card card--front" aria-label="Card front">
  <span class="brand-mark" aria-hidden="true"></span>
  <p class="abs brand-name">Velora Hypnotherapy</p>
  <span class="brand-rule" aria-hidden="true"></span>
  <p class="abs brand-url">www.veloraclinicalhypnotherapy.com.au</p>
  <p class="abs person-name">Daniel Wexford</p>
  <p class="abs person-role">Psychotherapy &amp; Hypnosis</p>
  <div class="portrait" role="img" aria-label="Portrait photo of the therapist, arms crossed, in a light shirt"></div>
  <svg class="wave" viewBox="0 0 368 110" aria-hidden="true">
    <path d="M0 48 Q150 12 368 22 L368 30 Q170 26 0 62 Z" fill="var(--swoosh-grey)"/>
    <path d="M0 66 Q170 30 368 34 L368 110 L0 110 Z" fill="var(--brand-blue)"/>
  </svg>
  <p class="abs front-phones">84261937 /0427591628</p>
  <p class="abs front-url">www.veloraclinicalhypnotherapy.com.au</p>
</section>

<section class="card card--back" aria-label="Card back">
  <p class="abs practice-name">Velora Clinical Hypnotherapy</p>
  <p class="abs practice-line practice-line--phone">By Appointment . Phone: 0427 591 628</p>
  <p class="abs practice-line practice-line--address">48 Linden Street, Kensington 3031</p>
  <p class="abs practice-email">hello@veloraclinicalhypnotherapy.com.au</p>
  <p class="abs appointments-title">Your Appointments</p>
  <ol class="appointment-list">
    <li>1. ____am/pm ____________ ___/___/___</li>
    <li>2. ____am/pm ____________ ___/___/___</li>
    <li>3. ____am/pm ____________ ___/___/___</li>
    <li>4. ____am/pm ____________ ___/___/___</li>
    <li>5. ____am/pm ____________ ___/___/___</li>
  </ol>
  <p class="abs reschedule">To reschedule your appointment,<br>please SMS or phone<br>0427 591 628 at least 24 hours prior to<br>your allocated time.&nbsp; Thank you.</p>
  <svg class="wave" viewBox="0 0 368 110" aria-hidden="true">
    <path d="M0 46 Q150 10 368 20 L368 28 Q170 24 0 60 Z" fill="var(--swoosh-grey)"/>
    <path d="M0 64 Q170 28 368 32 L368 110 L0 110 Z" fill="var(--brand-blue)"/>
  </svg>
  <p class="abs registration">NHRA Registration No. NPM058214</p>
</section>

</body>
</html>
```